Gobal construction supply company needs new business card design

I need a business card design for my global supply company using an existing logo. i will be looking to print these on rounded corner cards with the black background version of my logo on the back. on the front white background, my logo again and my simple details.

```html
<!DOCTYPE html>
<html lang="en">
<head>
<meta charset="utf-8">
<title>Kestrel Supply – Business Card</title>
<link href="https://fonts.googleapis.com/css2?family=Roboto:wght@400;500;700&display=swap" rel="stylesheet">
<style>
  :root {
    --backdrop: #bdbdbd;
    --card-dark: #1c1c1c;
    --card-light: #f3f3f3;
    --ink: #111111;
    --ink-soft: #4a4a4a;
    --accent: #d50000;
    --paper-white: #f2f2f2;
  }
  * { margin: 0; padding: 0; box-sizing: border-box; }
  html, body {
    width: 1200px;
    height: 960px;
    overflow: hidden;
    background: var(--backdrop);
    font-family: "Roboto", Arial, sans-serif;
  }
  .canvas { position: relative; width: 1200px; height: 960px; }

  .card {
    position: absolute;
    left: 300px;
    width: 600px;
    height: 342px;
    border-radius: 18px;
    overflow: hidden;
  }
  .card--back { top: 123px; background: var(--card-dark); }
  .card--front { top: 496px; background: var(--card-light); }

  /* back side wordmark */
  .back-mark {
    position: absolute;
    left: 0; right: 0; top: 140px;
    display: flex;
    justify-content: center;
    align-items: center;
    gap: 14px;
  }
  .back-mark__name {
    color: var(--paper-white);
    font-weight: 700;
    font-size: 46px;
    letter-spacing: 2px;
    line-height: 1;
  }
  .back-mark__dot {
    width: 34px; height: 34px;
    border-radius: 50%;
    background: var(--accent);
  }

  /* front side */
  .edge-bar {
    position: absolute;
    top: 94px;
    width: 15px;
    height: 150px;
  }
  .edge-bar--left { left: 0; background: var(--ink); }
  .edge-bar--right { right: 0; background: var(--accent); }

  .front-mark {
    position: absolute;
    left: 50px;
    top: 150px;
    width: 242px;
    display: flex;
    align-items: center;
    justify-content: center;
    gap: 10px;
  }
  .front-mark__name {
    color: var(--ink);
    font-weight: 700;
    font-size: 24px;
    letter-spacing: 0.5px;
    line-height: 1;
    white-space: nowrap;
  }
  .front-mark__square {
    width: 16px; height: 16px;
    background: var(--accent);
  }

  .contact {
    position: absolute;
    left: 329px;
    top: 90px;
  }
  .contact__name {
    font-weight: 500;
    font-size: 22px;
    color: var(--ink);
    letter-spacing: 0.3px;
    line-height: 26px;
  }
  .contact__role {
    font-weight: 500;
    font-size: 15px;
    color: var(--accent);
    line-height: 18px;
    margin-bottom: 10px;
  }
  .contact__line {
    font-size: 14.5px;
    color: var(--ink-soft);
    line-height: 18.5px;
  }
  .contact__group + .contact__group { margin-top: 10px; }
</style>
</head>
<body>
<div class="canvas">
  <section class="card card--back" aria-label="Card back">
    <div class="back-mark">
      <span class="back-mark__name">KESTREL</span>
      <span class="back-mark__dot"></span>
    </div>
  </section>

  <section class="card card--front" aria-label="Card front">
    <div class="edge-bar edge-bar--left"></div>
    <div class="edge-bar edge-bar--right"></div>

    <div class="front-mark">
      <span class="front-mark__name">KESTREL SUPPLY</span>
      <span class="front-mark__square"></span>
    </div>

    <div class="contact">
      <p class="contact__name">DANIEL HART</p>
      <p class="contact__role">CEO/FOUNDER</p>
      <div class="contact__group">
        <p class="contact__line">412 Harbour Street</p>
        <p class="contact__line">Millbrook, Ohio 45210</p>
      </div>
      <div class="contact__group">
        <p class="contact__line">555 214 7730</p>
        <p class="contact__line">daniel@kestrelsupply.com</p>
        <p class="contact__line">www.kestrelsupply.com</p>
      </div>
    </div>
  </section>
</div>
</body>
</html>
```